Moravel Aesthetic Doctor

I require an elegant, luxurious looking business card for my aesthetic business. I am a doctor and that will set me aside from competitors. I am planning to provide home and spa based treatments to clients with high expectations. I have attached my logo.

```html
<!DOCTYPE html>
<html lang="en">
<head>
<meta charset="utf-8">
<title>Moravel Aesthetic Doctor – Business Card</title>
<link href="https://fonts.googleapis.com/css2?family=Montserrat:wght@400;500&display=swap" rel="stylesheet">
<style>
  :root {
    --backdrop: #dcdde1;
    --blue-deep: #2a7bb8;
    --blue-light: #4aa6db;
    --blue-accent: #3a8fcf;
    --mark-tint: #a9d3ee;
    --ink: #2b2b2b;
    --paper: #ffffff;
  }
  * { margin: 0; padding: 0; box-sizing: border-box; }
  html, body {
    width: 1200px; height: 800px; overflow: hidden;
    background: var(--backdrop);
    font-family: "Montserrat", sans-serif;
  }
  .card {
    position: absolute; left: 389px; width: 461px; height: 263px;
  }
  .card-front {
    top: 93px;
    background: linear-gradient(35deg, var(--blue-deep) 0%, var(--blue-light) 100%);
    color: var(--paper);
  }
  .card-back { top: 422px; background: var(--paper); color: var(--ink); }

  /* brand block, front */
  .front-brand {
    position: absolute; left: 80px; top: 62px;
    display: flex; align-items: center; gap: 18px;
  }
  .brand-dot { border-radius: 50%; flex: none; }
  .front-brand .brand-dot { width: 78px; height: 78px; background: var(--mark-tint); opacity: .55; }
  .brand-name { font-weight: 400; line-height: 1; }
  .front-brand .brand-name { color: var(--paper); }
  .front-brand .brand-title { font-size: 38px; letter-spacing: 3px; display: block; }
  .front-brand .brand-sub { font-size: 14.5px; letter-spacing: 1.6px; display: block; margin-top: 8px; }

  .services {
    position: absolute; left: 0; right: 0; top: 186px;
    text-align: center; font-weight: 400;
  }
  .services-list { font-size: 11px; line-height: 13.5px; }
  .services-tagline { font-size: 14.5px; margin-top: 4px; }

  /* back */
  .back-brand {
    position: absolute; left: 43px; top: 104px;
    display: flex; align-items: center; gap: 10px;
  }
  .back-brand .brand-dot { width: 50px; height: 50px; border: 1.5px solid var(--blue-accent); }
  .back-brand .brand-name { color: var(--blue-accent); }
  .back-brand .brand-title { font-size: 24px; letter-spacing: 1.5px; display: block; }
  .back-brand .brand-sub { font-size: 9.6px; letter-spacing: .9px; display: block; margin-top: 5px; }

  .divider {
    position: absolute; left: 237px; top: 85px; width: 1px; height: 93px;
    background: var(--blue-accent);
  }
  .details { position: absolute; left: 250px; top: 80px; }
  .doctor-name { font-size: 14.5px; font-weight: 400; color: var(--ink); }
  .doctor-letters { font-size: 7px; color: var(--blue-accent); letter-spacing: .3px; margin-left: 2px; }
  .qualification { font-size: 11px; line-height: 13px; color: var(--blue-accent); margin-top: 5px; padding-left: 1px; }
  .contacts { list-style: none; margin-top: 10px; font-size: 11px; }
  .contacts li { display: flex; align-items: center; height: 14px; }
  .contacts li + li { margin-top: 0; }
  .contacts li:last-child { margin-top: 1px; }
  .contact-icon { width: 8px; height: 8px; margin: 0 6px 0 2px; flex: none; }
  .social { display: flex; gap: 6px; margin-left: 16px; }
  .social span { width: 8px; height: 8px; border-radius: 50%; background: var(--blue-accent); }
</style>
</head>
<body>

<section class="card card-front" aria-label="Business card front">
  <div class="front-brand">
    <span class="brand-dot"></span>
    <p class="brand-name">
      <span class="brand-title">MORAVEL</span>
      <span class="brand-sub">AESTHETIC DOCTOR</span>
    </p>
  </div>
  <div class="services">
    <p class="services-list">Dermal injectables - Plasma facials - Microneedling<br>Skin boosters - Excessive sweating</p>
    <p class="services-tagline">Home and Spa Based Treatments</p>
  </div>
</section>

<section class="card card-back" aria-label="Business card back">
  <div class="back-brand">
    <span class="brand-dot"></span>
    <p class="brand-name">
      <span class="brand-title">MORAVEL</span>
      <span class="brand-sub">AESTHETIC DOCTOR</span>
    </p>
  </div>
  <div class="divider"></div>
  <div class="details">
    <p class="doctor-name">Dr Elise Varnholt<span class="doctor-letters">MRCPCH MD</span></p>
    <p class="qualification">Australasian Diploma<br>of Aesthetic Medicine</p>
    <ul class="contacts">
      <li>
        <svg class="contact-icon" viewBox="0 0 10 10"><path d="M2 0.5 L3.6 0.5 L4.2 3 L3 3.8 Q4 6.2 6.2 7 L7 5.8 L9.5 6.4 L9.5 8 Q9.5 9.5 8 9.5 Q1.8 9 0.5 2 Q0.5 0.5 2 0.5Z" fill="#3a8fcf"/></svg>
        0800 555 019
      </li>
      <li>
        <svg class="contact-icon" viewBox="0 0 10 10"><rect x="0.5" y="2" width="9" height="6.5" fill="#3a8fcf"/><path d="M0.5 2 L5 5.6 L9.5 2" fill="none" stroke="#fff" stroke-width="0.9"/></svg>
        elise@moravel.co.nz
      </li>
      <li>
        <svg class="contact-icon" viewBox="0 0 10 10" fill="none" stroke="#8fa6b8" stroke-width="0.8"><circle cx="5" cy="5" r="4.4"/><ellipse cx="5" cy="5" rx="2" ry="4.4"/><path d="M0.6 5 H9.4 M1.3 2.8 H8.7 M1.3 7.2 H8.7"/></svg>
        www.moravel.co.nz
        <span class="social" aria-label="Social media"><span></span><span></span></span>
      </li>
    </ul>
  </div>
</section>

</body>
</html>
```